Norvane Letterhead Design Project

Design a new company letterhead utilizing our new logo and color scheme. Interested in professional letterhead and matching 2nd sheet versions.
Updates

I have uploaded windows format files now.  Originally only uploaded MAC file format.  Good luck!

Target Market(s)

Industry Executives, construction managers, well educated and discriminate personnel. Project needs to leave an impression and have impact but not be cluttered, busy or too in your face.

Industry/Entity Type

It Company

Requirements
Must have
• Clean, crisp look, true to new logo and color scheme, professional image. Should include spaces for company web address, address info and phone & fax numbers

```html
<!DOCTYPE html>
<html lang="en">
<head>
<meta charset="utf-8">
<title>Norvane Letterhead</title>
<link href="https://fonts.googleapis.com/css2?family=Arimo:wght@400;700&family=Saira:wght@700&display=swap" rel="stylesheet">
<style>
  :root {
    --backdrop: #e1e1df;
    --brand-orange: #d47a20;
    --brand-gray: #58585a;
    --paper: #ffffff;
    --ink: #2b2b2b;
    --watermark: #f4f4f4;
  }
  * { margin: 0; padding: 0; box-sizing: border-box; }
  html, body { width: 1200px; height: 845px; overflow: hidden; }
  body {
    position: relative;
    background: var(--backdrop);
    font-family: "Arimo", Arial, sans-serif;
  }
  .sheet { position: absolute; top: 132px; width: 389px; height: 551px; overflow: hidden; }
  .cover { left: 191px; background: var(--brand-orange); }
  .cover-mark {
    position: absolute; left: 157px; top: 209px;
    width: 74px; height: 74px; border-radius: 50%;
    background: var(--brand-gray);
  }
  .cover-name {
    position: absolute; left: 0; right: 0; top: 290px;
    text-align: center; color: var(--paper);
    font-family: "Saira", Arial, sans-serif; font-weight: 700;
    font-size: 36px; letter-spacing: 2px; line-height: 44px;
  }
  .letter { left: 635px; background: var(--paper); }
  .watermark {
    position: absolute; left: -10px; top: 40px;
    width: 420px; height: 440px; border-radius: 50%;
    background: var(--watermark);
  }
  .letter-header { position: absolute; left: 27px; top: 24px; display: flex; align-items: center; gap: 8px; }
  .header-mark { width: 31px; height: 31px; border-radius: 50%; background: var(--brand-gray); }
  .header-name {
    font-family: "Saira", Arial, sans-serif; font-weight: 700;
    font-size: 16px; color: var(--brand-orange); letter-spacing: 1px;
  }
  .contact {
    position: absolute; right: 18px; top: 23px;
    font-size: 5px; line-height: 6px; color: var(--brand-gray);
    list-style: none; text-align: right;
  }
  .contact li { display: flex; justify-content: flex-end; align-items: flex-start; gap: 4px; margin-bottom: 3px; }
  .contact svg { width: 6px; height: 6px; flex: none; fill: var(--brand-orange); }
  .letter-body {
    position: absolute; left: 31px; right: 29px; top: 127px;
    font-size: 6.3px; line-height: 8.1px; color: var(--ink); text-align: justify;
  }
  .letter-body h2 { font-size: 6.5px; font-weight: 700; margin-bottom: 8px; }
  .letter-body p { margin-bottom: 8px; }
  .letter-body .sign-off { margin-top: 18px; }
  .letter-footer { position: absolute; left: 0; right: 0; bottom: 0; height: 3px; display: flex; }
  .letter-footer .gray { width: 135px; background: var(--brand-gray); }
  .letter-footer .orange { flex: 1; background: var(--brand-orange); }
</style>
</head>
<body>
  <section class="sheet cover">
    <div class="cover-mark"></div>
    <div class="cover-name">NORVANE</div>
  </section>

  <section class="sheet letter">
    <div class="watermark"></div>
    <header class="letter-header">
      <div class="header-mark"></div>
      <div class="header-name">NORVANE</div>
    </header>
    <ul class="contact">
      <li><span>Your office<br>address here</span>
        <svg viewBox="0 0 10 10"><path d="M5 0a3.5 3.5 0 0 0-3.5 3.5C1.5 6 5 10 5 10s3.5-4 3.5-6.5A3.5 3.5 0 0 0 5 0zm0 5a1.5 1.5 0 1 1 0-3 1.5 1.5 0 0 1 0 3z"/></svg></li>
      <li><span>+00 1234 567<br>+00 1234 568</span>
        <svg viewBox="0 0 10 10"><path d="M2 1h2l1 2.5-1.3 1a6 6 0 0 0 2.8 2.8l1-1.3L10 7v2a1 1 0 0 1-1 1A9 9 0 0 1 0 1a1 1 0 0 1 1-1z"/></svg></li>
      <li><span>name@example.com<br>www.example.com</span>
        <svg viewBox="0 0 10 10"><path d="M0 2h10v6H0zM0 2l5 3.5L10 2" /></svg></li>
    </ul>
    <main class="letter-body">
      <h2>Lorem ipsum</h2>
      <p>Lorem ipsum dolor, consectetuer adipiscing elit, sed diam nonummy nibh euismod tincidunt ut laoreet dolore magna aliquam erat volutpat. Ut wisi enim ad minim veniam, quis nostrud exerci tation ullamcorper suscipit lobortis nisl ut aliquip ex ea commodo consequat. Duis autem vel eum iriure dolor in hendrerit in vulputate velit esse molestie consequat, vel illum dolore eu feugiat nulla facilisis minim</p>
      <p>Lorem ipsum dolor, consectetuer adipiscing elit, sed diam nonummy nibh euismod tincidunt ut laoreet dolore magna aliquam erat volutpat. Ut wisi enim ad minim veniam, quis nostrud exerci tation ullamcorper suscipit lobortis nisl ut aliquip ex ea commodo consequat. Duis autem vel eum iriure dolor in hendrerit in vulputate velit esse molestie consequat, vel illum dolore eu feugiat nulla facilisis minim</p>
      <p>Lorem ipsum dolor, consectetuer adipiscing elit, sed diam nonummy nibh euismod tincidunt ut laoreet dolore magna aliquam erat volutpat. Ut wisi enim ad minim veniam, quis nostrud exerci tation ullamcorper suscipit lobortis nisl ut aliquip ex ea commodo consequat. Duis autem vel eum iriure dolor in hendrerit in vulputate velit esse molestie consequat, vel illum dolore eu feugiat nulla facilisis minim</p>
      <p>Lorem ipsum dolor, consectetuer adipiscing elit, sed diam nonummy nibh euismod tincidunt ut laoreet dolore magna aliquam erat volutpat. Ut wisi enim ad minim veniam, quis nostrud exerci tation ullamcorper suscipit lobortis nisl ut aliquip ex ea commodo consequat. Duis autem vel eum iriure dolor in hendrerit in vulputate velit esse molestie consequat, vel illum dolore eu feugiat nulla facilisis minim</p>
      <p>Lorem ipsum dolor, consectetuer adipiscing elit, sed diam nonummy nibh euismod tincidunt ut laoreet dolore magna aliquam erat volutpat. Ut wisi enim ad minim veniam, quis nostrud exerci tation ullamcorper suscipit lobortis nisl ut aliquip ex ea commodo consequat. Duis autem vel eum iriure dolor in hendrerit in vulputate velit esse molestie consequat, vel illum dolore eu feugiat nulla facilisis minim</p>
      <p>Lorem ipsum dolor, consectetuer adipiscing elit, sed diam nonummy nibh euismod tincidunt ut laoreet dolore magna aliquam erat volutpat. Ut wisi enim ad minim veniam, quis nostrud exerci tation ullamcorper suscipit lobortis nisl ut aliquip ex ea commodo consequat. Duis autem vel eum iriure dolor in hendrerit in vulputate velit esse molestie consequat, vel illum dolore eu feugiat nulla facilisis minim</p>
      <p class="sign-off">Yours Sincerely,</p>
    </main>
    <footer class="letter-footer"><span class="gray"></span><span class="orange"></span></footer>
  </section>
</body>
</html>
```